Communication and Marketing agency needs a new presentation card

We are a group of communication and marketing agencies specialized in companies that are in the logistics and industrial sector. The head agency is TELVANO Grupo and the group consists of 4 agencies: TELVANO Media, TELVANO Digital, TELVANO Research and DifundeEnPantalla. We hace 4 offices in Spain (Madrid, Barcelona, Valencia and Murcia). We are looking for a clean and attractive design that transmits our experience, brand presence in the market and knowledge to those who receive the card.It has to maintain the colors of the logo that is attached.
Target Market(s)
logistics and industrial sector
Marketing department
Contact Information for Business Card
Clean and attractive design

```html
<!DOCTYPE html>
<html lang="es">
<head>
<meta charset="utf-8">
<title>TELVANO Grupo – Tarjeta de presentación</title>
<link rel="stylesheet" href="https://fonts.googleapis.com/css2?family=Jost:wght@400;500&family=Barlow+Condensed:wght@600&display=swap">
<style>
  :root {
    --brand-red: #b31d28;
    --brand-grey: #636363;
    --text-grey: #555555;
    --paper: #ffffff;
    --backdrop: #1f1f1f;
  }
  * { box-sizing: border-box; margin: 0; padding: 0; }
  html, body { width: 1125px; height: 1200px; overflow: hidden; }
  body {
    background: var(--backdrop);
    font-family: "Jost", "Futura", sans-serif;
    position: relative;
  }
  .card {
    position: absolute;
    left: 150px;
    width: 826px;
    height: 472px;
    overflow: hidden;
  }
  .card--front { top: 98px; background: var(--paper); }
  .card--back { top: 631px; background: var(--brand-red); }

  .card__shapes { position: absolute; inset: 0; }

  /* Front: brand block */
  .front-brand {
    position: absolute;
    right: 50px;
    top: 62px;
    text-align: right;
    color: var(--brand-red);
    font-weight: 400;
    line-height: 1;
  }
  .front-brand__name { font-size: 62px; letter-spacing: 3px; }
  .front-brand__unit { font-size: 38px; margin-top: 2px; }
  .front-offices {
    position: absolute;
    right: 48px;
    top: 172px;
    font-family: "Barlow Condensed", "Arial Narrow", sans-serif;
    font-weight: 600;
    font-size: 21px;
    letter-spacing: 0.5px;
    color: var(--text-grey);
  }

  /* Front: contact list */
  .contact-list {
    position: absolute;
    left: 44px;
    top: 308px;
    list-style: none;
    color: var(--paper);
    font-size: 22px;
    line-height: 27px;
  }
  .contact-list li { display: flex; align-items: center; gap: 14px; }
  .contact-list svg { width: 20px; height: 20px; flex: none; }

  /* Front: holder */
  .holder {
    position: absolute;
    right: 50px;
    top: 384px;
    text-align: right;
    color: var(--paper);
  }
  .holder__name { font-size: 31px; line-height: 1.1; }
  .holder__role { font-size: 21px; line-height: 1.2; }

  /* Back: group brand */
  .group-brand {
    position: absolute;
    left: 203px;
    top: 124px;
    width: 420px;
    text-align: right;
    color: var(--paper);
    line-height: 1;
  }
  .group-brand__name { font-size: 88px; letter-spacing: 5px; font-weight: 400; text-align: center; }
  .group-brand__unit { font-size: 50px; font-weight: 400; margin-top: 6px; }

  /* Back: agencies band */
  .agency-band {
    position: absolute;
    left: 0; right: 0;
    top: 333px;
    height: 92px;
    background: var(--paper);
    display: flex;
    justify-content: space-around;
    align-items: center;
    padding: 0 18px;
  }
  .agency {
    text-align: right;
    line-height: 1;
    font-weight: 400;
  }
  .agency__name { font-size: 29px; letter-spacing: 1.5px; }
  .agency__unit { font-size: 19px; margin-top: 2px; }
  .agency--grey { color: var(--brand-grey); }
  .agency--red { color: var(--brand-red); }
  .agency--stacked { text-align: left; font-size: 25px; letter-spacing: 1px; }
</style>
</head>
<body>

<section class="card card--front" aria-label="Anverso de la tarjeta">
  <svg class="card__shapes" viewBox="0 0 826 472" aria-hidden="true">
    <polygon points="377,374 826,374 826,472 439,472" fill="var(--brand-grey)"/>
    <polygon points="0,283 312,283 439,472 0,472" fill="var(--brand-red)"/>
    <line x1="312" y1="283" x2="439" y2="472" stroke="var(--paper)" stroke-width="3"/>
  </svg>

  <div class="front-brand">
    <div class="front-brand__name">TELVANO</div>
    <div class="front-brand__unit">Media</div>
  </div>
  <div class="front-offices">LORVEDA/CASTRELO/VILMONTE/ARANZA</div>

  <ul class="contact-list">
    <li>
      <svg viewBox="0 0 20 20" aria-hidden="true"><path fill="#fff" d="M2 8c0-3 4-5 8-5s8 2 8 5l-4 1-1-2H7L6 9 2 8zm3 3h10l1 6H4l1-6zm5 1.5a2 2 0 100 4 2 2 0 000-4z"/></svg>
      <span>910 555 214</span>
    </li>
    <li>
      <svg viewBox="0 0 20 20" aria-hidden="true"><rect x="5" y="1" width="10" height="18" rx="2" fill="#fff"/><rect x="7" y="4" width="6" height="10" fill="var(--brand-red)"/></svg>
      <span>600 555 318</span>
    </li>
    <li>
      <svg viewBox="0 0 20 20" aria-hidden="true"><rect x="2" y="5" width="16" height="11" fill="#fff"/><path d="M2 5l8 6 8-6" stroke="var(--brand-red)" stroke-width="1.5" fill="none"/></svg>
      <span>lvidal@telvano.es</span>
    </li>
    <li>
      <svg viewBox="0 0 20 20" aria-hidden="true"><rect x="3" y="3" width="14" height="14" fill="#fff"/></svg>
      <span>lorenzovidal</span>
    </li>
    <li>
      <svg viewBox="0 0 20 20" aria-hidden="true"><circle cx="10" cy="10" r="8" fill="#fff"/><path d="M2 10h16M10 2v16" stroke="var(--brand-red)" stroke-width="1.2"/></svg>
      <span>telvano.es</span>
    </li>
  </ul>

  <div class="holder">
    <div class="holder__name">Lorenzo Vidal</div>
    <div class="holder__role">Director</div>
  </div>
</section>

<section class="card card--back" aria-label="Reverso de la tarjeta">
  <div class="group-brand">
    <div class="group-brand__name">TELVANO</div>
    <div class="group-brand__unit">Grupo</div>
  </div>

  <div class="agency-band">
    <div class="agency agency--grey">
      <div class="agency__name">TELVANO</div>
      <div class="agency__unit">Digital</div>
    </div>
    <div class="agency agency--red">
      <div class="agency__name">TELVANO</div>
      <div class="agency__unit">Media</div>
    </div>
    <div class="agency agency--grey">
      <div class="agency__name">TELVANO</div>
      <div class="agency__unit">Research</div>
    </div>
    <div class="agency agency--red agency--stacked">
      <div>DIFUNDE</div>
      <div>ENPANTALLA</div>
    </div>
  </div>
</section>

</body>
</html>
```